Kelumo.cn needs pages to be re-designed

www.kelumo.cn is our current new site which was launched in April.
We're a financial services website in the crowdfunding space in China to connect borrower's and lender's.

test.kelumo.cn is our test site
u: test
p: newtest
http://test.kelumo.cn/
http://test.kelumo.cn/user/accounts/new_lender
http://test.kelumo.cn/user/accounts/new_borrower
http://test.kelumo.cn/introductions/protection
http://test.kelumo.cn/introductions
http://test.kelumo.cn/introductions/kelumo_admin
http://test.kelumo.cn/introductions/contact
Some of the pages have pop-ups in the bloc's of the pages. Please click the links, to see more content.

User's currently criticize the website for being:
- Too Western looking
- Too simple, too little content
- Content NOT in the pop-ups are too simple
- Pictures are too big and too much blank space
- Relevant information is not there when needed
- The pictures are too generic

What we would like to do is re-design those pages with the same color scheme and style to be more compelling, efficient, non-intimidating and easy-to-use. Our audience is Ages 25-35 predominantly male investors.
We are looking for more ideas to make the content match the style, while bridging western and chinese design. Our ultimate goal is to increase registrants to the website and highlight our core competitive advantages.

Some competitors websites are:
www.fobuxiqi.com
www.tamev.com
www.zzzlendo.com

Reason: Not enough good designs that follow the prompt. Same style, better information layout!

Reason: Still have not received a design we're satisfied with

Reason: WE DONT WANT A COMPLETE REDESIGN OF PAGES . KEEP THE EXACT SAME COLOR AND STYLE - WE WANT CONTENT RE-DESIGN! THE BLOCS ARE TOO SIMPLE - WE WANT MORE CONTENT INSIDE.

Reason: no new designs

Reason: no new designs

Reason: other non-registered pages need to be re-designed

```html
<!DOCTYPE html>
<html lang="zh-CN">
<head>
<meta charset="utf-8">
<title>Kelumo.cn 可路摩贷</title>
<link href="https://fonts.googleapis.com/css2?family=Noto+Sans+SC:wght@300;400;500;700&family=Roboto:wght@300;400;500&display=swap" rel="stylesheet">
<style>
:root{
  --green:#82d420;
  --green-dark:#6cbc14;
  --blue:#27a9e1;
  --blue-dark:#1a8fc6;
  --ink:#333333;
  --muted:#8a8a8a;
  --dark:#3b3b3b;
  --line:#e3e3e3;
  --pale:#f3f5f6;
  --beige:#eff2e2;
  --gray-band:#ececec;
  --orange:#f7a234;
  --yellow:#fad94c;
  --red:#ef6363;
  --purple:#9a7a9d;
  --white:#ffffff;
}
*{box-sizing:border-box;margin:0;padding:0}
html,body{width:1200px;height:2573px;overflow:hidden}
body{font-family:"Noto Sans SC",sans-serif;color:var(--ink);background:var(--white);position:relative}
.abs{position:absolute}
a{color:inherit;text-decoration:none}

/* header */
.site-header{position:absolute;left:0;top:0;width:1200px;height:88px;background:var(--white)}
.brand{position:absolute;left:100px;top:18px;display:flex;align-items:center;gap:10px}
.brand-dot{width:50px;height:50px;border-radius:50%;background:var(--green)}
.brand-name{font-size:22px;font-weight:500;color:var(--ink);line-height:1}
.brand-sub{font-size:11px;color:var(--green);margin-top:3px}
.main-nav{position:absolute;right:100px;top:34px;display:flex;gap:44px;font-size:14px;color:var(--ink)}
.main-nav span{display:flex;align-items:center;gap:6px}
.main-nav svg{width:14px;height:14px}

/* hero */
.hero{position:absolute;left:0;top:88px;width:1200px;height:480px;background:linear-gradient(90deg,#d9dde0 0%,#eef2f5 40%,#dde6ee 100%);overflow:hidden}
.hero-photo{position:absolute;left:0;top:0;width:500px;height:400px;background:radial-gradient(ellipse at 45% 55%,#9cb56a 0%,#c7cfc0 40%,rgba(220,225,228,0) 75%)}
.hero-title{position:absolute;left:535px;top:105px;font-family:"Roboto",sans-serif;font-weight:300;font-size:37px;line-height:44px;color:#2b2b2b;letter-spacing:.3px}
.hero-text{position:absolute;left:535px;top:200px;width:560px;font-family:"Roboto",sans-serif;font-size:19px;line-height:25px;color:#3a3a3a}
.read-more{position:absolute;left:535px;top:307px;width:237px;height:44px;border-radius:22px;background:var(--green);color:var(--white);font-family:"Roboto",sans-serif;font-weight:500;font-size:16px;display:flex;align-items:center;padding-left:68px}
.read-more::before{content:"";position:absolute;left:-2px;top:-4px;width:52px;height:52px;border-radius:50%;background:var(--white);border:3px solid var(--green)}
.hero-dots{position:absolute;left:1028px;top:22px;display:flex;gap:6px}
.hero-dots i{width:11px;height:11px;border-radius:50%;background:#c9ced2;display:block}
.hero-dots i.on{background:var(--white);border:2px solid var(--green)}
.hero-next{position:absolute;left:1086px;top:222px}
.press-row{position:absolute;left:98px;top:424px;display:flex;gap:16px;align-items:center}
.press-row i{display:block;height:30px;border-radius:3px;background:#8c8f93;opacity:.75}

/* tabs */
.tabs{position:absolute;left:0;top:568px;width:1200px;height:59px;display:flex}
.tab{flex:1;background:var(--dark);color:var(--white);font-size:25px;display:flex;align-items:center;justify-content:center;gap:14px}
.tab.active{background:var(--green)}
.tab svg{width:34px;height:34px}
.tagline{position:absolute;left:0;top:627px;width:1200px;height:38px;background:var(--beige);color:var(--green-dark);font-size:11px;text-align:center;line-height:38px}

.notice{position:absolute;left:0;top:665px;width:1200px;height:50px;background:var(--white);font-size:14px}
.notice .title{position:absolute;left:175px;top:14px}
.notice .date{position:absolute;left:828px;top:14px;color:#555}
.pill-outline{position:absolute;left:928px;top:10px;width:100px;height:30px;border:1px solid var(--blue);border-radius:15px;color:var(--blue);font-size:13px;text-align:center;line-height:28px}

.ticker{position:absolute;left:0;top:715px;width:1200px;height:55px;background:#f4f6f1;display:flex;gap:28px;padding-left:128px;align-items:center;font-size:14px;color:var(--ink)}
.ticker b{color:var(--green-dark);font-weight:400;margin-right:6px}

.stats{position:absolute;left:0;top:770px;width:1200px;height:103px;background:var(--pale)}
.stat{position:absolute;top:28px;border-right:1px solid #cfd6da;padding-right:14px}
.stat .num{font-family:"Roboto",sans-serif;font-size:27px;color:var(--blue);line-height:30px}
.stat .lbl{font-size:9px;color:#666;margin-top:3px}
.start-btn{position:absolute;left:834px;top:25px;width:193px;height:54px;border-radius:27px;background:var(--blue);color:var(--white);font-size:24px;font-weight:500;display:flex;align-items:center;padding-left:64px}
.start-btn::before{content:"";position:absolute;left:2px;top:2px;width:50px;height:50px;border-radius:50%;background:var(--white)}
.start-btn svg{position:absolute;left:12px;top:12px}

/* invest list */
.section-title{position:absolute;left:173px;top:902px;font-size:25px;color:var(--green-dark);font-weight:500}
.loan-table{position:absolute;left:173px;top:951px;width:854px;border-collapse:collapse;font-size:12px}
.loan-table th{background:#f2f2f2;height:50px;text-align:left;font-weight:400;color:#555;font-size:13px}
.loan-table td{height:51px;border-bottom:1px solid var(--line);color:#aaa}
.loan-table tr:nth-child(even) td{background:#fafafa}
.loan-table th:first-child,.loan-table td:first-child{padding-left:12px}
.grade{display:inline-flex;gap:6px;align-items:center;vertical-align:middle}
.g{width:24px;height:24px;border-radius:50%;background:var(--green);color:var(--white);font-size:13px;font-weight:700;text-align:center;line-height:24px}
.zhuan{width:24px;height:24px;border-radius:50%;background:#5ab5e6;color:var(--white);font-size:12px;text-align:center;line-height:24px}
.prog{display:inline-flex;align-items:center;gap:10px}
.btn-bid{display:inline-block;width:96px;height:27px;border-radius:14px;background:var(--blue);color:var(--white);font-size:12px;text-align:center;line-height:27px}
.btn-bid.done{background:#b5b5b5}

/* fixed products */
.products{position:absolute;left:0;top:1357px;width:1200px;height:118px;display:flex}
.prod-head{width:277px;background:var(--blue);color:var(--white);padding:12px 0 0 118px;font-size:24px;position:relative}
.prod-head i{position:absolute;left:118px;height:5px;background:var(--white);display:block}
.prod{flex:1;position:relative;padding:10px 0 0 10px;color:var(--ink)}
.prod .p1{font-size:14px}
.prod .rate{position:absolute;right:12px;top:6px;font-family:"Roboto",sans-serif;font-weight:500;font-size:25px;color:#1f1f1f}
.prod .p2{font-size:14px;margin-top:13px}
.prod .buy{position:absolute;left:10px;top:78px;width:97px;height:28px;border-radius:14px;background:var(--dark);color:var(--white);font-size:13px;text-align:center;line-height:28px}

/* features */
.features{position:absolute;left:0;top:1475px;width:1200px;height:263px;background:var(--gray-band)}
.feature{position:absolute;top:35px;width:340px;margin-left:-170px;text-align:center}
.feature .circle{width:110px;height:110px;border-radius:50%;background:var(--white);margin:0 auto;display:flex;align-items:center;justify-content:center;box-shadow:0 2px 4px rgba(0,0,0,.05)}
.feature h3{font-size:25px;font-weight:400;margin-top:30px;color:#333}
.feature p{font-size:13px;color:#666;margin-top:4px}
.feature.hl h3,.feature.hl p{color:var(--blue)}

/* value */
.value{position:absolute;left:0;top:1738px;width:1200px;height:252px;background:var(--white)}
.value .divider{position:absolute;left:590px;top:20px;width:5px;height:196px;background:linear-gradient(90deg,#ddd,#fff)}
.value h4{position:absolute;left:327px;top:8px;font-size:21px;color:var(--blue);font-weight:500}
.value .desc{position:absolute;left:327px;top:44px;width:225px;font-size:10px;line-height:16px;color:#555}
.gray-btn{position:absolute;left:325px;top:152px;width:95px;height:28px;border-radius:14px;background:#7b7b7b;color:var(--white);font-size:13px;text-align:center;line-height:28px}
.ins-names{position:absolute;left:700px;top:42px;font-size:17px;font-weight:500;color:var(--green-dark)}
.ins-text{position:absolute;left:620px;top:148px;width:400px;text-align:center;font-size:11px;line-height:17px;color:#333}
.ins-links{position:absolute;left:735px;top:188px;font-size:13px;color:var(--blue);display:flex;gap:16px}

/* service */
.service{position:absolute;left:0;top:1990px;width:1200px;height:263px;background:var(--green);color:var(--white)}
.service h2{position:absolute;left:207px;top:52px;font-size:24px;font-weight:400}
.service p{position:absolute;left:207px;top:105px;width:500px;font-size:12px;line-height:20px}
.service .more{position:absolute;left:207px;top:173px;font-size:13px;text-decoration:underline}
.service .ring{position:absolute;left:818px;top:50px;width:160px;height:160px;border-radius:50%;border:3px solid var(--white);display:flex;align-items:center;justify-content:center}

/* partners */
.partners{position:absolute;left:0;top:2253px;width:1200px;height:92px}
.partners .lbl{position:absolute;left:207px;top:22px;font-size:12px}
.partner-row{position:absolute;left:207px;top:46px;display:flex;gap:22px;align-items:center}
.partner-row i{display:block;height:26px;border-radius:3px;background:#d9dce0}

/* footer */
.site-footer{position:absolute;left:0;top:2345px;width:1200px;height:175px;background:var(--dark);color:#eee}
.foot-links{position:absolute;left:173px;top:20px;font-size:13px;display:flex;gap:16px}
.foot-friends{position:absolute;left:173px;top:45px;font-size:13px;display:flex;gap:16px}
.foot-service{position:absolute;left:173px;top:82px;font-size:13px;display:flex;align-items:center;gap:12px}
.foot-service i{width:20px;height:20px;border-radius:50%;background:#bdbdbd;display:block}
.online{width:97px;height:28px;border-radius:14px;background:#222;color:#fff;text-align:center;line-height:28px;margin-left:12px}
.hotline{position:absolute;right:173px;top:18px;text-align:right}
.hotline .t{font-size:13px}
.hotline .n{font-family:"Roboto",sans-serif;font-size:25px;font-weight:500;margin-top:6px}
.hotline .h{font-size:9px;margin-top:2px}
.certs{position:absolute;left:268px;top:137px;display:flex;gap:24px}
.certs i{display:block;height:26px;background:#d5d5d5;border-radius:2px}
.bottom{position:absolute;left:0;top:2520px;width:1200px;height:53px;background:var(--white)}
.bottom .copy{position:absolute;left:173px;top:21px;font-size:10px;color:#888}
.bottom .mini{position:absolute;right:120px;top:14px;display:flex;align-items:center;gap:8px;font-size:17px;font-weight:500;color:var(--ink)}
.bottom .mini i{width:26px;height:26px;border-radius:50%;background:var(--green);display:block}
</style>
</head>
<body>

<header class="site-header">
  <div class="brand">
    <span class="brand-dot"></span>
    <div><div class="brand-name">可路摩贷</div><div class="brand-sub">kelumo.cn</div></div>
  </div>
  <nav class="main-nav">
    <span><svg viewBox="0 0 14 14"><path d="M7 1 L12 3 V7 C12 10 9.5 12 7 13 C4.5 12 2 10 2 7 V3 Z" fill="#555"/></svg>安全</span>
    <span><svg viewBox="0 0 14 14"><circle cx="7" cy="7" r="5.5" fill="none" stroke="#555" stroke-width="2"/><circle cx="7" cy="7" r="2" fill="#555"/></svg>投资</span>
    <span><svg viewBox="0 0 14 14"><rect x="2" y="3" width="10" height="10" rx="1" fill="none" stroke="#555" stroke-width="2"/></svg>贷款</span>
    <span><svg viewBox="0 0 14 14"><rect x="3" y="6" width="8" height="7" fill="#555"/><path d="M4.5 6 V4 a2.5 2.5 0 0 1 5 0 V6" fill="none" stroke="#555" stroke-width="1.6"/></svg>登录 ▾</span>
  </nav>
</header>

<section class="hero">
  <div class="hero-photo" role="img" aria-label="双手捧着土壤中长出的上升箭头形状的绿色植物，背景为城市"></div>
  <div class="hero-dots"><i></i><i class="on"></i><i></i><i></i><i></i></div>
  <h1 class="hero-title">LOREM IPSUM DOLOR SIT AMET,<br>CONSECTETUER ...</h1>
  <p class="hero-text">Ut wisi enim ad minim veniam, quis nostrud exerci tation ullamcorper suscipit lobortis nisl ut aliquip ex ea commodo consequat.</p>
  <a class="read-more">READ MORE</a>
  <svg class="hero-next" width="14" height="26" viewBox="0 0 14 26"><path d="M2 2 L12 13 L2 24" fill="none" stroke="#fff" stroke-width="2"/></svg>
  <div class="press-row">
    <i style="width:58px"></i><i style="width:62px"></i><i style="width:56px"></i><i style="width:72px"></i><i style="width:108px"></i><i style="width:88px"></i><i style="width:78px"></i><i style="width:126px"></i><i style="width:66px"></i><i style="width:34px"></i>
  </div>
</section>

<div class="tabs">
  <div class="tab"><svg viewBox="0 0 34 34"><rect x="3" y="5" width="28" height="20" fill="none" stroke="#fff" stroke-width="2"/><path d="M7 20 L13 14 L18 18 L27 9" fill="none" stroke="#fff" stroke-width="2"/><path d="M12 25 L9 31 M22 25 L25 31" stroke="#fff" stroke-width="2"/></svg>高回报</div>
  <div class="tab active"><svg viewBox="0 0 34 34"><path d="M17 2 L30 7 V16 C30 24 24 29 17 32 C10 29 4 24 4 16 V7 Z" fill="none" stroke="#fff" stroke-width="2"/><path d="M10 17 L15 22 L25 11" fill="none" stroke="#fff" stroke-width="3"/></svg>安全</div>
  <div class="tab"><svg viewBox="0 0 34 34"><circle cx="17" cy="17" r="14" fill="none" stroke="#fff" stroke-width="2"/><path d="M17 17 V3 A14 14 0 0 1 30 22 Z" fill="#fff"/><path d="M17 17 L5 25 A14 14 0 0 0 20 31 Z" fill="#fff"/></svg>高效</div>
</div>
<div class="tagline">可路摩贷是一个安全、高效、透明的投资平台。</div>

<div class="notice">
  <span class="title">可路摩网 邀请有返利啦</span>
  <span class="date">2014-06-05</span>
  <a class="pill-outline">更多公告</a>
</div>

<div class="ticker">
  <span><b>成功贷款</b>10000元 年利率 15.0%</span>
  <span><b>成功投资</b>2000元 年利率 15.0%</span>
  <span><b>成功贷款</b>20000元 年利率 15.0%</span>
  <span><b>成功投资</b>3000元 年利率 15.0%</span>
</div>

<section class="stats">
  <div class="stat" style="left:175px"><div class="num">¥56573</div><div class="lbl">资金需求</div></div>
  <div class="stat" style="left:320px"><div class="num">14.68%</div><div class="lbl">平均收益率</div></div>
  <div class="stat" style="left:475px;border:none"><div class="num">11.8月</div><div class="lbl">平均期限</div></div>
  <a class="start-btn"><svg width="30" height="30" viewBox="0 0 30 30"><circle cx="15" cy="15" r="12" fill="none" stroke="#27a9e1" stroke-width="4"/><circle cx="15" cy="15" r="5" fill="#27a9e1"/><path d="M15 15 L27 3" stroke="#27a9e1" stroke-width="3"/></svg>开始投资</a>
</section>

<h2 class="section-title">投资列表</h2>
<table class="loan-table">
  <thead><tr><th style="width:115px">借款标题</th><th style="width:170px">信用等级</th><th style="width:125px">年利率</th><th style="width:115px">金额</th><th style="width:95px">期限</th><th style="width:120px">进度</th><th></th></tr></thead>
  <tbody>
    <tr><td>fafafa</td><td><span class="grade"><span class="g">S</span><svg width="22" height="24" viewBox="0 0 22 24"><path d="M11 1 L20 4 V11 C20 17 15 21 11 23 C7 21 2 17 2 11 V4 Z" fill="#3a9a6a"/><path d="M6 11 L10 15 L16 8" stroke="#fff" stroke-width="2.4" fill="none"/></svg></span></td><td>15.0%</td><td>30000元</td><td>13个月</td><td><span class="prog"><svg width="22" height="22"><circle cx="11" cy="11" r="10" fill="#e8e8e8"/></svg>0.0%</span></td><td><a class="btn-bid">开始出借</a></td></tr>
    <tr><td>fafafa</td><td><span class="grade"><span class="g">S</span><svg width="22" height="24" viewBox="0 0 22 24"><path d="M11 1 L20 4 V11 C20 17 15 21 11 23 C7 21 2 17 2 11 V4 Z" fill="#3a9a6a"/><path d="M6 11 L10 15 L16 8" stroke="#fff" stroke-width="2.4" fill="none"/></svg></span></td><td>12.0%</td><td>12000元</td><td>4个月</td><td><span class="prog"><svg width="22" height="22"><circle cx="11" cy="11" r="10" fill="#e8e8e8"/></svg>0.0%</span></td><td><a class="btn-bid">开始出借</a></td></tr>
    <tr><td>fafafa</td><td><span class="grade"><span class="g">B</span><svg width="22" height="24" viewBox="0 0 22 24"><path d="M11 1 L20 4 V11 C20 17 15 21 11 23 C7 21 2 17 2 11 V4 Z" fill="#3a9a6a"/><path d="M6 11 L10 15 L16 8" stroke="#fff" stroke-width="2.4" fill="none"/></svg></span></td><td>15.0%</td><td>30000元</td><td>0个月</td><td><span class="prog"><svg width="22" height="22"><circle cx="11" cy="11" r="10" fill="#e8e8e8"/></svg>0.0%</span></td><td><a class="btn-bid">开始出借</a></td></tr>
    <tr><td>fafafa</td><td><span class="grade"><span class="g">B</span><svg width="22" height="24" viewBox="0 0 22 24"><path d="M11 1 L20 4 V11 C20 17 15 21 11 23 C7 21 2 17 2 11 V4 Z" fill="#3a9a6a"/><path d="M6 11 L10 15 L16 8" stroke="#fff" stroke-width="2.4" fill="none"/></svg><span class="zhuan">转</span></span></td><td>15.0%</td><td>30000元</td><td>5个月</td><td><span class="prog"><svg width="22" height="22"><circle cx="11" cy="11" r="10" fill="#e8e8e8"/></svg>0.0%</span></td><td><a class="btn-bid">开始出借</a></td></tr>
    <tr><td>fafafa</td><td><span class="grade"><span class="g">A</span><svg width="22" height="24" viewBox="0 0 22 24"><path d="M11 1 L20 4 V11 C20 17 15 21 11 23 C7 21 2 17 2 11 V4 Z" fill="#3a9a6a"/><path d="M6 11 L10 15 L16 8" stroke="#fff" stroke-width="2.4" fill="none"/></svg><span class="zhuan">转</span></span></td><td>15.0%</td><td>30000元</td><td>12个月</td><td><span class="prog"><svg width="22" height="22"><circle cx="11" cy="11" r="10" fill="#e8e8e8"/><path d="M11 1 A10 10 0 0 0 11 21 Z" fill="#82d420"/></svg>50.0%</span></td><td><a class="btn-bid done">开始出借</a></td></tr>
    <tr><td>fafafa</td><td><span class="grade"><span class="g">A</span><svg width="22" height="24" viewBox="0 0 22 24"><path d="M11 1 L20 4 V11 C20 17 15 21 11 23 C7 21 2 17 2 11 V4 Z" fill="#3a9a6a"/><path d="M6 11 L10 15 L16 8" stroke="#fff" stroke-width="2.4" fill="none"/></svg></span></td><td>15.0%</td><td>30000元</td><td>6个月</td><td><span class="prog"><svg width="22" height="22"><circle cx="11" cy="11" r="10" fill="#82d420"/></svg>100.0%</span></td><td><a class="btn-bid done">开始出借</a></td></tr>
  </tbody>
</table>

<section class="products">
  <div class="prod-head">固定产品<i style="top:60px;width:100px"></i><i style="top:72px;width:82px"></i><i style="top:84px;width:50px"></i></div>
  <div class="prod" style="background:var(--orange)"><div class="p1">3个月回报率</div><div class="rate">10.0%</div><div class="p2">剩下9笔，每笔1.0万元</div><a class="buy">现在投资</a></div>
  <div class="prod" style="background:var(--yellow)"><div class="p1">6个月回报率</div><div class="rate">11.0%</div><div class="p2">剩下9笔，每笔1.0万元</div><a class="buy">现在投资</a></div>
  <div class="prod" style="background:var(--red)"><div class="p1">9个月回报率</div><div class="rate">12.0%</div><div class="p2">剩下9笔，每笔1.0万元</div><a class="buy">现在投资</a></div>
  <div class="prod" style="background:var(--purple);flex:1.48"><div class="p1">12个月回报率</div><div class="rate" style="right:auto;left:140px">13.0%</div><div class="p2">剩下9笔，每笔1.0万元</div><a class="buy">现在投资</a></div>
</section>

<section class="features">
  <div class="feature" style="left:316px"><div class="circle"><svg width="50" height="54" viewBox="0 0 50 54"><circle cx="25" cy="30" r="20" fill="none" stroke="#333" stroke-width="3"/><rect x="20" y="2" width="10" height="5" fill="#333"/><path d="M25 30 V18" stroke="#333" stroke-width="3"/></svg></div><h3>3分钟内即可完成投资</h3><p>注册、验证身份和电子邮件</p></div>
  <div class="feature hl" style="left:598px"><div class="circle"><svg width="52" height="46" viewBox="0 0 52 46"><path d="M4 14 L26 3 L48 14 Z" fill="#27a9e1"/><rect x="8" y="17" width="36" height="3" fill="#27a9e1"/><rect x="11" y="22" width="5" height="15" fill="#27a9e1"/><rect x="20" y="22" width="5" height="15" fill="#27a9e1"/><rect x="28" y="22" width="5" height="15" fill="#27a9e1"/><rect x="37" y="22" width="5" height="15" fill="#27a9e1"/><rect x="5" y="39" width="42" height="4" fill="#27a9e1"/></svg></div><h3>充值账户</h3><p>支持更多银行</p></div>
  <div class="feature" style="left:880px"><div class="circle"><svg width="44" height="54" viewBox="0 0 44 54"><path d="M18 52 V22 a3 3 0 0 1 6 0 V34 l10 2 c3 1 4 3 3 7 l-3 9" fill="none" stroke="#333" stroke-width="2.5"/><path d="M21 4 V10 M9 10 l4 4 M33 10 l-4 4 M5 22 h6 M31 22 h6" stroke="#333" stroke-width="2.5"/></svg></div><h3>选择您的投资方式</h3><p>手动投资、固定产品或快速投资</p></div>
</section>

<section class="value">
  <svg class="abs" style="left:190px;top:50px" width="118" height="110" viewBox="0 0 118 110"><rect x="10" y="66" width="18" height="42" fill="#333"/><rect x="40" y="50" width="18" height="58" fill="#333"/><rect x="70" y="58" width="18" height="50" fill="#333"/><rect x="98" y="38" width="18" height="70" fill="#333"/><path d="M6 40 L40 18 L70 32 L110 6" fill="none" stroke="#27a9e1" stroke-width="4"/><circle cx="6" cy="40" r="5" fill="#27a9e1"/><circle cx="40" cy="18" r="5" fill="#27a9e1"/><circle cx="70" cy="32" r="5" fill="#27a9e1"/><circle cx="110" cy="6" r="5" fill="#27a9e1"/></svg>
  <h4>每年回报率10%-15%</h4>
  <p class="desc">可路摩贷采用可持续的方式保持收益均衡。我们关注您财务的长期健康状况，以帮助您实现稳定且高于平均水平的回报。</p>
  <a class="gray-btn">了解详情</a>
  <div class="divider"></div>
  <div class="ins-names">华辰人寿 <span style="color:#333">+</span> Marlow 安衡保险经纪</div>
  <svg class="abs" style="left:640px;top:78px" width="360" height="66" viewBox="0 0 360 66"><path d="M12 16 L24 12 L36 16 V28 C36 36 30 40 24 42 C18 40 12 36 12 28 Z" fill="#333"/><path d="M18 26 L23 31 L31 22" stroke="#fff" stroke-width="3" fill="none"/><rect x="50" y="20" width="205" height="18" fill="#82d420"/><path d="M252 6 L290 29 L252 52 Z" fill="#82d420"/><g fill="#3a9a6a"><path d="M300 4 L312 0 L324 4 V14 C324 20 318 24 312 26 C306 24 300 20 300 14 Z"/><path d="M300 38 L312 34 L324 38 V48 C324 54 318 58 312 60 C306 58 300 54 300 48 Z"/><path d="M328 20 L340 16 L352 20 V30 C352 36 346 40 340 42 C334 40 328 36 328 30 Z"/></g></svg>
  <p class="ins-text">我们是唯一与华辰人寿和非洲最大的保险公司合作的P2P平台<br>提供最安全的理财选择</p>
  <div class="ins-links"><a>了解合作</a><a>了解安全</a></div>
</section>

<section class="service">
  <h2>高效服务，让您满意</h2>
  <p>2天内获得贷款或3分钟内完成投资，您可以随时随地了解您的资金流向。我们是一个快速高效的平台，让您自助自持拥有完全控制权。</p>
  <a class="more">了解详情</a>
  <div class="ring"><svg width="70" height="82" viewBox="0 0 70 82"><circle cx="35" cy="18" r="15" fill="#fff"/><path d="M4 82 V58 C4 44 16 36 35 36 C54 36 66 44 66 58 V82 Z" fill="#fff"/><circle cx="35" cy="56" r="8" fill="#82d420"/><rect x="32" y="63" width="6" height="6" fill="#82d420"/></svg></div>
</section>

<section class="partners">
  <div class="lbl">合作伙伴</div>
  <div class="partner-row"><i style="width:110px"></i><i style="width:100px"></i><i style="width:150px"></i><i style="width:26px"></i><i style="width:60px"></i><i style="width:160px"></i></div>
</section>

<footer class="site-footer">
  <div class="foot-links"><a>投资</a><a>贷款</a><a>安全</a><a>媒体</a><a>合作</a><a>关于我们</a><a>联系我们</a><a>加入我们</a><a>帮助中心</a></div>
  <div class="foot-friends"><span>友情链接：贷友之家</span><a>理财天眼</a><a>理财俱乐部</a></div>
  <div class="foot-service">客户服务：<i></i><i></i><i></i><i></i><a class="online">在线客服</a></div>
  <div class="hotline"><div class="t">客服电话</div><div class="n">400-088-2746</div><div class="h">周一至周五 9:00-18:00</div></div>
  <div class="certs"><i style="width:22px"></i><i style="width:96px"></i><i style="width:96px"></i><i style="width:80px"></i><i style="width:84px"></i><i style="width:124px"></i></div>
</footer>

<div class="bottom">
  <div class="copy">Copyright © 2014 京ICP备 20480517号 版权所有：北京可路摩信息技术有限公司</div>
  <div class="mini"><i></i>可路摩贷</div>
</div>

</body>
</html>
```